Wordpress Design for a Private Label BBQ Brand

For our new brand, we'd need a new Wordpress website. We'd prefer to run the website on Wordpress

We'd like to include the following
- space for description of the brand
- space for product portfolio (not a shop!)
- space for socials
- space for support
- space for contact

```html
<!DOCTYPE html>
<html lang="en">
<head>
<meta charset="utf-8">
<title>Emberly — Portable BBQ Grills</title>
<link rel="stylesheet" href="https://fonts.googleapis.com/css2?family=Cinzel:wght@700;900&family=Montserrat:wght@400;500;600;700&display=swap">
<style>
:root{
  --ink:#111111;
  --nav:#1b1b1b;
  --orange:#ec5a1e;
  --red:#d8321c;
  --blue:#2f6cb8;
  --blue-light:#4a93e6;
  --cream:#fdf4d5;
  --news-bg:#edf1f8;
  --text:#333333;
  --muted:#8a8a8a;
  --star:#f5b400;
  --white:#ffffff;
}
*{box-sizing:border-box;margin:0;padding:0}
html,body{width:1200px;height:4448px;overflow:hidden}
body{font-family:"Montserrat",sans-serif;color:var(--text);background:var(--white)}
section,header,footer,.nav{position:relative;display:block;width:1200px;overflow:hidden}
.abs{position:absolute}
.serif{font-family:"Cinzel",serif;font-weight:900}
.flame-dot{display:inline-block;width:14px;height:14px;border-radius:50%;background:var(--red);vertical-align:middle;margin-right:12px}

/* top bar */
.topbar{height:48px;background:var(--ink)}
.topbar .call{left:648px;top:16px;font-size:12px;font-weight:700;color:var(--blue-light);letter-spacing:.5px;display:flex;align-items:center;gap:8px;white-space:nowrap}
.topbar .call b{color:var(--white)}
.social{top:9px;width:30px;height:30px;border-radius:50%;border:2px solid #555;display:block}

/* nav */
.nav{height:85px;background:var(--nav)}
.brand{left:98px;top:24px;display:flex;align-items:center;gap:10px;font-family:"Cinzel",serif;font-weight:700;font-size:34px;line-height:38px;color:var(--white)}
.brand i{width:16px;height:16px;border-radius:50%;background:var(--orange)}
.menu a{position:absolute;top:36px;font-size:12px;font-weight:700;color:var(--white);letter-spacing:1px;text-decoration:none;white-space:nowrap}
.menu a.active{color:var(--orange)}
.btn-nav{left:976px;top:31px;width:124px;height:37px;background:linear-gradient(90deg,var(--orange),var(--red));color:var(--white);font-size:11px;font-weight:700;display:flex;align-items:center;justify-content:center}

/* hero */
.hero{height:459px}
.hero .photo{inset:0;background:linear-gradient(110deg,#2c3a22 0%,#4f5a33 35%,#3b2f25 60%,#6c6f63 100%)}
.hero .shade{inset:0;background:linear-gradient(90deg,rgba(0,0,0,.55),rgba(0,0,0,.1))}
.hero .kicker{left:102px;top:115px;font-size:15px;font-weight:700;letter-spacing:2px;color:var(--blue-light)}
.hero h1{left:92px;top:140px;font-size:60px;line-height:70px;color:var(--white);letter-spacing:1px;white-space:nowrap}
.hero .sub{left:98px;top:219px;font-size:13px;font-weight:700;color:var(--white)}
.hero .cta{left:95px;top:278px;width:155px;height:38px;background:linear-gradient(90deg,var(--orange),var(--red));color:var(--white);font-size:12px;font-weight:700;display:flex;align-items:center;justify-content:center}

/* tiles */
.tiles{height:385px;display:flex}
.tile{position:relative;width:600px;height:385px}
.tile.products{background:linear-gradient(135deg,#2a5aa7,#3b73c6 60%,#2b62b5)}
.tile.accessories{background:linear-gradient(120deg,#e45a20,#ef7d2b 50%,#d73f1e)}
.tile .kicker{position:absolute;top:152px;font-size:14px;color:var(--white)}
.tile h2{position:absolute;top:172px;font-size:29px;color:var(--white);white-space:nowrap}

/* about */
.about{height:418px;background:var(--cream)}
.about .product-photo{left:164px;top:85px;width:294px;height:328px;background:radial-gradient(ellipse at center,#3a3a3a 0%,#2a2a2a 45%,rgba(253,244,213,0) 70%)}
.about .label{left:599px;top:87px;font-size:12px;font-weight:700;color:var(--ink)}
.about h2{left:599px;top:106px;font-size:30px;color:var(--red);white-space:nowrap}
.about p{left:599px;top:162px;width:494px;font-size:12px;line-height:20px;color:var(--ink)}
.about .btn{left:599px;top:304px;width:178px;height:46px;background:var(--blue);color:var(--white);font-size:12px;font-weight:700;display:flex;align-items:center;justify-content:center}

/* products */
.products-sec{height:720px}
.products-sec .label{left:0;width:1200px;top:70px;text-align:center;font-size:12px;font-weight:700;color:var(--ink)}
.products-sec h2{left:0;width:1200px;top:98px;text-align:center;font-size:40px;color:var(--ink);white-space:nowrap}
.products-sec h2 em{font-style:normal;color:var(--red)}
.arrow{top:331px;width:48px;height:48px;border-radius:50%;background:var(--white);box-shadow:0 2px 10px rgba(0,0,0,.12);display:flex;align-items:center;justify-content:center}
.card{top:180px;width:300px;text-align:center}
.card .slot{height:255px;display:flex;align-items:center;justify-content:center}
.card .pic{background:linear-gradient(180deg,#2c2c2c,#4a4a4a);border-radius:6px}
.card h3{margin-top:28px;font-size:19px;font-weight:700;color:var(--red)}
.card p{margin-top:12px;font-size:12px;color:var(--ink)}
.stars{margin-top:16px;display:flex;justify-content:center}
.products-sec .see-all{left:497px;top:606px;width:208px;height:47px;border:2px solid var(--blue);color:var(--blue);font-size:12px;font-weight:700;display:flex;align-items:center;justify-content:center}

/* how it works */
.how{height:311px}
.how .photo{inset:0;background:linear-gradient(180deg,#3b3128,#1b1a1a 60%,#262626)}
.how h2{left:0;width:1200px;top:78px;text-align:center;font-size:40px;color:var(--white)}
.how .dot{left:593px;top:42px;width:14px;height:14px;border-radius:50%;background:var(--red)}
.how .play{left:545px;top:148px}

/* news */
.news{height:708px;background:var(--news-bg)}
.news h2{left:0;width:1200px;top:88px;text-align:center;font-size:40px;color:var(--ink)}
.news h2 em{font-style:normal;color:var(--red)}
.post{top:209px;width:309px;height:337px;background:var(--white)}
.post .pic{height:176px;background:linear-gradient(135deg,#2a1a12,#8a3a14 50%,#e07a22)}
.post .date{position:absolute;left:14px;top:12px;background:var(--blue);color:var(--white);font-size:11px;font-weight:700;padding:3px 7px;border-radius:2px}
.post h3{margin:20px 16px 0;font-size:20px;font-weight:600;color:var(--ink);white-space:nowrap}
.post p{margin:10px 16px 0;font-size:11.5px;line-height:19px;color:var(--muted)}
.pager{left:585px;top:598px;display:flex;gap:6px}
.pager span{width:16px;height:16px;border-radius:50%;border:1.5px solid #666;background:var(--white)}
.pager span.on{background:var(--blue);border-color:var(--blue)}

/* why buy */
.why{height:307px;background:linear-gradient(90deg,#3a7bcb,#2c5aa5)}
.why h2{left:0;width:1200px;top:46px;text-align:center;font-size:28px;color:var(--white)}
.feature{top:126px;width:260px;text-align:center}
.feature .ico{margin:0 auto;width:84px;height:84px;border-radius:50%;background:var(--white);display:flex;align-items:center;justify-content:center}
.feature h3{margin-top:22px;font-family:"Cinzel",serif;font-weight:700;font-size:18px;color:var(--white);white-space:nowrap}

/* contact */
.contact{height:644px;background:var(--cream)}
.contact .frame{left:90px;top:158px;width:532px;height:352px;background:var(--white);box-shadow:0 4px 20px rgba(0,0,0,.08)}
.contact .frame div{position:absolute;inset:14px;background:linear-gradient(135deg,#4d6a2e,#a6874e 50%,#6b4d33)}
.contact h2{left:667px;top:120px;font-size:30px;color:var(--red);white-space:nowrap}
.contact .intro{left:669px;top:188px;width:440px;font-size:11px;line-height:19px;color:var(--text)}
.field{left:668px;width:434px;background:var(--white);font-size:11px;font-weight:700;color:#555;padding:12px 16px}
.contact .send{left:668px;top:519px;width:156px;height:42px;background:var(--blue);color:var(--white);font-size:12px;font-weight:700;display:flex;align-items:center;justify-content:center}

/* footer */
.footer{height:363px;background:var(--ink)}
.footer .mark{left:0;width:1200px;top:68px;display:flex;flex-direction:column;align-items:center;gap:14px;font-family:"Cinzel",serif;font-weight:700;font-size:24px;color:var(--white)}
.footer .mark i{width:18px;height:18px;border-radius:50%;background:var(--orange)}
.footer .links{left:0;width:1200px;top:174px;display:flex;justify-content:center;gap:28px;font-size:12px;color:var(--white)}
.footer .legal{left:0;width:1200px;top:224px;display:flex;justify-content:center;gap:8px;font-size:12px;color:var(--white)}
.footer .rule{left:152px;top:267px;width:974px;height:1px;background:var(--red)}
.footer .copy{left:0;width:1200px;top:307px;text-align:center;font-size:12px;color:var(--white)}
</style>
</head>
<body>

<header class="topbar">
  <div class="abs call">
    <svg width="14" height="14" viewBox="0 0 24 24"><path d="M6.6 10.8a15 15 0 0 0 6.6 6.6l2.2-2.2a1 1 0 0 1 1-.25 11.4 11.4 0 0 0 3.6.6 1 1 0 0 1 1 1V20a1 1 0 0 1-1 1A17 17 0 0 1 3 4a1 1 0 0 1 1-1h3.5a1 1 0 0 1 1 1c0 1.25.2 2.45.6 3.6a1 1 0 0 1-.25 1z" fill="#4a93e6"/></svg>
    CALL US TODAY! <b>555-014-2760</b>
  </div>
  <span class="abs social" style="left:928px"></span>
  <span class="abs social" style="left:975px"></span>
  <span class="abs social" style="left:1021px"></span>
  <span class="abs social" style="left:1070px"></span>
</header>

<nav class="nav">
  <div class="abs brand"><i></i>EMBERLY</div>
  <div class="menu">
    <a class="active" style="left:445px">HOME</a>
    <a style="left:536px">ABOUT US</a>
    <a style="left:654px">PRODUCTS</a>
    <a style="left:777px">NEWS</a>
    <a style="left:865px">CONTACT</a>
  </div>
  <div class="abs btn-nav">CONTACT NOW</div>
</nav>

<section class="hero">
  <div class="abs photo" role="img" aria-label="People enjoying a backyard barbecue around a kettle grill"></div>
  <div class="abs shade"></div>
  <div class="abs kicker">WELCOME TO EMBERLY</div>
  <h1 class="abs serif">GRILL LIKE A PRO</h1>
  <div class="abs sub">PORTABLE BBQ GRILLS, ADDONS AND GRILLING ACCESSORIES</div>
  <div class="abs cta">CONTACT US</div>
</section>

<section class="tiles">
  <div class="tile products" role="img" aria-label="Grill grate with blue overlay">
    <div class="kicker" style="left:98px">CHECK OUT OUR PRODCUTS</div>
    <h2 class="serif" style="left:98px">BE A PITMASTER</h2>
  </div>
  <div class="tile accessories" role="img" aria-label="Man grilling outdoors with orange overlay">
    <div class="kicker" style="left:65px;top:155px">CHECK OUT OUR ACCESSORIES</div>
    <h2 class="serif" style="left:65px">EMBERLY DIFFERENCE</h2>
  </div>
</section>

<section class="about">
  <div class="abs product-photo" role="img" aria-label="Two black ceramic kamado grills, one open"></div>
  <div class="abs label">ABOUT EMBERLY</div>
  <h2 class="abs serif"><span class="flame-dot"></span>WHO WE ARE</h2>
  <p class="abs">Lorem Ipsum is simply dummy text of the printing and typesetting industry. Lorem Ipsum has been the industry's standard dummy text ever since the 1500s, when an unknown printer took a galley of type and scrambled it to make a type specimen book. It has survived not only five centuries, but also the leap into electronic typesetting</p>
  <div class="abs btn">MORE ABOUT US</div>
</section>

<section class="products-sec">
  <svg width="0" height="0" style="position:absolute"><defs><path id="star" d="M8 0l2.4 5 5.4.6-4 3.7 1.1 5.4L8 12l-4.9 2.7 1.1-5.4-4-3.7 5.4-.6z"/></defs></svg>
  <div class="abs label">MEET THE</div>
  <h2 class="abs serif"><span class="flame-dot"></span><em>EMBERLY</em> PRODUCTS</h2>
  <div class="abs arrow" style="left:76px"><svg width="14" height="14" viewBox="0 0 14 14"><path d="M9 2L4 7l5 5" stroke="#333" stroke-width="2" fill="none"/></svg></div>
  <div class="abs arrow" style="left:1071px"><svg width="14" height="14" viewBox="0 0 14 14"><path d="M5 2l5 5-5 5" stroke="#333" stroke-width="2" fill="none"/></svg></div>
  <div class="abs card" style="left:92px">
    <div class="slot"><div class="pic" role="img" aria-label="Black kamado grill on stand" style="width:150px;height:250px"></div></div>
    <h3>Product Name</h3><p>Desription goes here</p>
    <div class="stars"><svg width="100" height="16" viewBox="0 0 100 16"><g fill="#f5b400"><use href="#star"/><use href="#star" x="21"/><use href="#star" x="42"/><use href="#star" x="63"/><use href="#star" x="84"/></g></svg></div>
  </div>
  <div class="abs card" style="left:444px">
    <div class="slot"><div class="pic" role="img" aria-label="Case of grilling tools" style="width:186px;height:175px"></div></div>
    <h3>Product Name</h3><p>Desription goes here</p>
    <div class="stars"><svg width="100" height="16" viewBox="0 0 100 16"><g fill="#f5b400"><use href="#star"/><use href="#star" x="21"/><use href="#star" x="42"/><use href="#star" x="63"/><use href="#star" x="84"/></g></svg></div>
  </div>
  <div class="abs card" style="left:797px">
    <div class="slot"><div class="pic" role="img" aria-label="Tongs, fork and spatula set" style="width:150px;height:170px"></div></div>
    <h3>Product Name</h3><p>Desription goes here</p>
    <div class="stars"><svg width="100" height="16" viewBox="0 0 100 16"><g fill="#f5b400"><use href="#star"/><use href="#star" x="21"/><use href="#star" x="42"/><use href="#star" x="63"/><use href="#star" x="84"/></g></svg></div>
  </div>
  <div class="abs see-all">SEE ALL OUR PRODUCTS</div>
</section>

<section class="how">
  <div class="abs photo" role="img" aria-label="Meat and vegetable skewers on a grill"></div>
  <span class="abs dot"></span>
  <h2 class="abs serif">HOW IT WORKS</h2>
  <svg class="abs play" width="110" height="110" viewBox="0 0 110 110">
    <circle cx="55" cy="55" r="53" fill="none" stroke="#2f6cb8" stroke-width="2"/>
    <circle cx="55" cy="55" r="42" fill="none" stroke="#2f6cb8" stroke-width="2"/>
    <circle cx="55" cy="55" r="30" fill="#fff"/>
    <path d="M48 42l18 13-18 13z" fill="#111"/>
  </svg>
</section>

<section class="news">
  <h2 class="abs serif"><span class="flame-dot"></span><em>EMBERLY</em> NEWS</h2>
  <article class="abs post" style="left:110px">
    <div class="pic" role="img" aria-label="Corn and skewers on a kettle grill"></div>
    <span class="date">July 30,2019</span>
    <h3>Lorem Ipsum is a dummy</h3>
    <p>Lorem Ipsum is simply dummy text of the a printing and typesetting ever since indus-try Lorem Ipsum is simply dummy text of</p>
  </article>
  <article class="abs post" style="left:444px">
    <div class="pic" role="img" aria-label="Flames rising from a grill"></div>
    <span class="date">July 25,2019</span>
    <h3>Lorem Ipsum is a dummy</h3>
    <p>Lorem Ipsum is simply dummy text of the a printing and typesetting ever since indus-try Lorem Ipsum is simply dummy text of</p>
  </article>
  <article class="abs post" style="left:777px">
    <div class="pic" role="img" aria-label="Grilling at night over open fire"></div>
    <span class="date">July 22,2019</span>
    <h3>Lorem Ipsum is a dummy</h3>
    <p>Lorem Ipsum is simply dummy text of the a printing and typesetting ever since indus-try Lorem Ipsum is simply dummy text of</p>
  </article>
  <div class="abs pager"><span></span><span class="on"></span><span></span></div>
</section>

<section class="why">
  <h2 class="abs serif"><span class="flame-dot" style="background:#fff"></span>WHY BUY FROM EMBERLY</h2>
  <div class="abs feature" style="left:57px">
    <div class="ico"><svg width="36" height="36" viewBox="0 0 36 36" fill="none" stroke="#d8321c" stroke-width="2"><circle cx="18" cy="15" r="9"/><path d="M12 22l-3 11 9-4 9 4-3-11"/></svg></div>
    <h3>WARRANTIES</h3>
  </div>
  <div class="abs feature" style="left:322px">
    <div class="ico"><svg width="36" height="36" viewBox="0 0 36 36" fill="none" stroke="#d8321c" stroke-width="2"><path d="M18 3l12 5v9c0 8-6 13-12 16C12 30 6 25 6 17V8z"/><path d="M13 18l4 4 7-8"/></svg></div>
    <h3>EXCLUSIVE PRODUCTS</h3>
  </div>
  <div class="abs feature" style="left:588px">
    <div class="ico"><svg width="36" height="36" viewBox="0 0 36 36" fill="none" stroke="#d8321c" stroke-width="2"><path d="M6 6l24 24M30 6L6 30"/><circle cx="8" cy="8" r="3"/><circle cx="28" cy="28" r="3"/></svg></div>
    <h3>GENUINE PARTS</h3>
  </div>
  <div class="abs feature" style="left:853px">
    <div class="ico"><svg width="36" height="36" viewBox="0 0 36 36" fill="none" stroke="#d8321c" stroke-width="2"><circle cx="18" cy="18" r="12"/><circle cx="18" cy="18" r="5"/></svg></div>
    <h3>CUSTOMER SERVICE</h3>
  </div>
</section>

<section class="contact">
  <div class="abs frame"><div role="img" aria-label="Family sharing a meal outdoors beside a gas grill"></div></div>
  <h2 class="abs serif"><span class="flame-dot"></span>YOU CAN WRITE US</h2>
  <p class="abs intro">Lorem Ipsum is simply dummy text of the printing and typesetting industry. When an unknown printer took a galley.</p>
  <div class="abs field" style="top:246px;height:43px">Name</div>
  <div class="abs field" style="top:310px;height:42px">Email</div>
  <div class="abs field" style="top:372px;height:124px">Message</div>
  <div class="abs send">CONTACT NOW</div>
</section>

<footer class="footer">
  <div class="abs mark"><i></i>EMBERLY</div>
  <div class="abs links"><span>Home</span><span>About us</span><span>Products</span><span>Accessories</span><span>Contact</span></div>
  <div class="abs legal"><span>Privacy Policy</span><span>Legal Notice</span></div>
  <div class="abs rule"></div>
  <div class="abs copy">© Copyright 2023 by emberly</div>
</footer>

</body>
</html>
```